Sophisticated, clean website reflecting my feminine, playful side to sell my abstract art,

I need a website no more than 3 pages to showcase my paintings, a little about me and some contact info. I do abstracts so looking for something a little edgy, yet feminine and current.
Updates

Hi there, These are some artists websites that I Iike: Marnelvoss.com (I like how airy it is) peterwallombry.com garethpolvens.com (I like how it scrolls) I'll need a place for a photo ( a headshot-i do not have it yet so I'll need to be able to upload that later) as well as an area for my bio. Also, it's important that I will be able to upload any new photos and descriptions easily so it should be user friendly. Lastly, I like in a sunny place so would like to have this seem upbeat and playful as that is how i like to paint. thanks-I'm trying to upload my photos now -

Target Market(s)

ppl ages 35-70 who want large scale art for their homes

Industry/Entity Type

art

Coding

Coded - Design and coding required

Number of Pages Required

3 page

Colors

Designer to choose colors to be used in the design.

Requirements
Must have
• photos of my art, a place for my bio, be easy to reach me. tasteful-nothing too "in your face" -my clients are pretty high end and organized. They like clean lines
Nice to have
• sophisticated background, muted tones in the back-similar clean font throughout-no cursive
Should not have
• too many dark areas. Too many blocks of color. Too serious.

```html
<!DOCTYPE html>
<html lang="en">
<head>
<meta charset="utf-8">
<title>Lena Hartwell Art</title>
<link rel="stylesheet" href="https://fonts.googleapis.com/css2?family=Baloo+2:wght@400;500&display=swap">
<style>
  :root {
    --paper: #ffffff;
    --ink: #111111;
    --text: #2a2a2a;
    --muted: #6b6b6b;
    --rule: #9a9a9a;
    --rose: #e3a3b3;
    --glow: #f3a64a;
    --footer: #000000;
    --footer-text: #d9d9d9;
  }
  * { box-sizing: border-box; margin: 0; padding: 0; }
  html, body { width: 1200px; height: 857px; overflow: hidden; background: var(--paper); }
  body { position: relative; font-family: "Baloo 2", sans-serif; color: var(--text); }

  .intro { position: absolute; left: 0; top: 0; width: 600px; height: 750px; background: var(--paper); }

  .menu-toggle { position: absolute; left: 42px; top: 16px; width: 70px; height: 40px; }

  .brand-name {
    position: absolute; left: 72px; top: 140px;
    font-size: 34px; font-weight: 400; letter-spacing: 14px; line-height: 1;
    color: var(--ink);
  }

  .headshot {
    position: absolute; left: 42px; top: 200px; width: 142px; height: 113px;
    border-radius: 26px 0 26px 0;
    background: linear-gradient(135deg, #eceef0 0%, #e2d6cc 45%, #b79a82 60%, #e9eaec 100%);
  }

  .bio {
    position: absolute; left: 42px; top: 337px; width: 330px;
    font-size: 13.3px; line-height: 21px; color: var(--text);
  }

  .signature {
    position: absolute; left: 42px; top: 442px; width: 108px; height: 30px;
    background: linear-gradient(90deg, #d8d8d8, #ececec);
    border-radius: 3px;
  }

  .cursor-label {
    position: absolute; font-size: 12px; letter-spacing: 0.3px; color: var(--muted);
    text-transform: uppercase; line-height: 1;
  }
  .cursor-label--links { left: 57px; top: 547px; }
  .cursor-label--default { left: 371px; top: 690px; width: 92px; text-align: center; }

  .cursor-demo { position: absolute; left: 0; top: 0; }

  .slide-dots { position: absolute; left: 567px; top: 465px; width: 14px; height: 116px; }

  .featured-painting {
    position: absolute; left: 600px; top: 0; width: 600px; height: 750px;
    background:
      radial-gradient(circle at 62% 60%, #8a4a3a 0%, rgba(138,74,58,0) 22%),
      radial-gradient(circle at 30% 25%, #e6a8c4 0%, rgba(230,168,196,0) 40%),
      radial-gradient(circle at 80% 80%, #d7a089 0%, rgba(215,160,137,0) 40%),
      linear-gradient(135deg, #d9a2b8 0%, #e8c2c6 40%, #c98a82 70%, #e3b3bf 100%);
  }

  .site-footer {
    position: absolute; left: 0; top: 750px; width: 1200px; height: 107px;
    background: var(--footer);
  }
  .site-footer p {
    position: absolute; left: 0; right: 0; top: 80px;
    text-align: center; font-size: 11.5px; color: var(--footer-text); line-height: 1;
  }
</style>
</head>
<body>
  <main class="intro">
    <svg class="menu-toggle" viewBox="0 0 70 40" aria-label="Menu">
      <line x1="0" y1="4" x2="50" y2="4" stroke="#111" stroke-width="2.2"/>
      <line x1="0" y1="16" x2="50" y2="16" stroke="#111" stroke-width="2.2"/>
      <line x1="0" y1="31" x2="26" y2="31" stroke="#111" stroke-width="2.2"/>
      <circle cx="49" cy="19" r="15" fill="none" stroke="#e3a3b3" stroke-width="1"/>
    </svg>

    <div class="brand-name">LH</div>

    <div class="headshot" role="img" aria-label="Portrait photo of the artist"></div>

    <p class="bio">Lorem ipsum dolor sit amet, consectetuer adipiscing elit. Aenean commodo ligula eget dolor. Aenean massa. Cum sociis natoque penatibus et magnis dis parturient montes, nascetur ridiculus mus.</p>

    <div class="signature" role="img" aria-label="Handwritten signature of Lena Hartwell"></div>

    <span class="cursor-label cursor-label--links">Mouse cursor on links</span>

    <svg class="cursor-demo" width="600" height="750" viewBox="0 0 600 750" aria-hidden="true">
      <defs>
        <radialGradient id="cursorGlow">
          <stop offset="0" stop-color="#f3a64a" stop-opacity="0.95"/>
          <stop offset="0.35" stop-color="#f6bf78" stop-opacity="0.55"/>
          <stop offset="1" stop-color="#fde8d0" stop-opacity="0"/>
        </radialGradient>
      </defs>
      <line x1="133" y1="567" x2="100" y2="671" stroke="#a0a0a0" stroke-width="0.8"/>
      <circle cx="117" cy="655" r="75" fill="none" stroke="#111" stroke-width="1"/>
      <circle cx="101" cy="668" r="15" fill="none" stroke="#e3a3b3" stroke-width="1"/>
      <line x1="101" y1="671" x2="133" y2="640" stroke="#111" stroke-width="1.4"/>
      <polyline points="114,640 133,640 133,659" fill="none" stroke="#111" stroke-width="1.4"/>

      <circle cx="415" cy="546" r="55" fill="url(#cursorGlow)"/>
      <line x1="417.5" y1="581" x2="417.5" y2="682" stroke="#9a9a9a" stroke-width="0.8"/>
    </svg>

    <span class="cursor-label cursor-label--default">Mouse cursor</span>

    <svg class="slide-dots" viewBox="0 0 14 116" aria-label="Gallery slides">
      <rect x="3" y="2" width="8" height="8" transform="rotate(45 7 6)" fill="#666" stroke="#666" stroke-width="1.4"/>
      <rect x="3" y="27" width="8" height="8" transform="rotate(45 7 31)" fill="none" stroke="#555" stroke-width="1.4"/>
      <rect x="3" y="52" width="8" height="8" transform="rotate(45 7 56)" fill="none" stroke="#555" stroke-width="1.4"/>
      <rect x="3" y="77" width="8" height="8" transform="rotate(45 7 81)" fill="none" stroke="#555" stroke-width="1.4"/>
      <rect x="3" y="102" width="8" height="8" transform="rotate(45 7 106)" fill="none" stroke="#555" stroke-width="1.4"/>
    </svg>
  </main>

  <div class="featured-painting" role="img" aria-label="Abstract painting of a large rose in pinks, peach and rust with dark brushstroke outlines"></div>

  <footer class="site-footer">
    <p>©2022 Lena Hartwell Art. All rights reserved.</p>
  </footer>
</body>
</html>
```